National online rug retailer needs a home page design

See the FloorNest logo and create a home page design around that color theme. Details are spelled out in word document uploaded below.

Apparently this website did not take my attachement showing the logo and basic requirements.  If you would send me your email address, I will send you the attachment directly.
Best regards,
Tom Vance
tvance@mrdcorp.example

Target Market(s)

The target market is home owners 25 to 75 years old with combined incomes over $100,000 per year.

Industry/Entity Type

Online

Requirements
Must have
• Lots of white space with black letters and creative use of red and possibly one other color. Would like a compelling call to action button.

```html
<!DOCTYPE html>
<html lang="en">
<head>
<meta charset="utf-8">
<title>FloorNest.com – Home</title>
<link href="https://fonts.googleapis.com/css2?family=Source+Sans+3:wght@300;400;600;700&family=Roboto+Condensed:wght@400&display=swap" rel="stylesheet">
<style>
:root{
  --red:#d0021b;
  --red-dark:#a80014;
  --black:#111;
  --ink:#222;
  --muted:#555;
  --page:#f1f1f1;
  --panel:#fff;
  --line:#d8d8d8;
  --nav-top:#5a5a5a;
  --nav-bot:#2e2e2e;
  --ad-blue:#1e4fa3;
}
*{box-sizing:border-box;margin:0;padding:0}
html,body{width:1040px;height:1200px;overflow:hidden}
body{font-family:"Source Sans 3",sans-serif;color:var(--ink);background:#fff;position:relative;font-size:10px}

/* header */
.site-header{position:absolute;left:0;top:0;width:1040px;height:102px;background:linear-gradient(#1a1a1a,#0a0a0a)}
.brand{position:absolute;left:134px;top:20px;display:flex;align-items:center;gap:4px}
.brand-mark{width:14px;height:14px;background:var(--red)}
.brand-name{font-size:28px;color:#fff;font-weight:400;letter-spacing:.5px}
.brand-tag{position:absolute;left:192px;top:60px;color:#ddd;font-size:8px}
.search{position:absolute;left:430px;top:33px;width:175px;height:37px;border:2px solid #555;border-radius:3px;background:#2a2a2a;color:#ddd;font-size:11px;padding:10px 10px}
.search svg{position:absolute;right:10px;top:9px}
.top-btns{position:absolute;left:659px;top:10px;display:flex;gap:4px}
.btn-light{background:linear-gradient(#fafafa,#cfcfcf);border-radius:2px;color:#111;font-size:9px;height:19px;padding:3px 7px;display:flex;align-items:center;gap:3px}
.btn-light .hi{color:var(--red)}
.phone{position:absolute;left:684px;top:39px;color:var(--red);font-size:13px;display:flex;align-items:center;gap:6px}
.phone b{font-size:16px;font-weight:600}
.acct-btns{position:absolute;left:662px;top:70px;display:flex;gap:6px}
.live-chat{position:absolute;left:819px;top:71px;color:#fff;font-size:12px;display:flex;align-items:center;gap:6px}
.chat-ico{width:18px;height:15px;background:#7ec229;border-radius:3px}
.main-nav{position:absolute;left:0;top:102px;width:1040px;height:31px;background:linear-gradient(var(--nav-top),var(--nav-bot));display:flex;justify-content:center}
.main-nav ul{list-style:none;display:flex}
.main-nav li{color:#fff;font-size:11px;padding:9px 0;text-align:center;border-left:1px solid #222;box-shadow:inset 1px 0 #777}
.main-nav li:first-child{border-left:none;box-shadow:none}

/* hero band */
.hero-band{position:absolute;left:0;top:133px;width:1040px;height:360px;background:var(--page);box-shadow:0 3px 4px rgba(0,0,0,.08)}
.browse{position:absolute;left:135px;top:143px;width:179px;height:337px;background:var(--panel);box-shadow:0 1px 3px rgba(0,0,0,.25)}
.browse h2{background:var(--black);color:var(--red);font-weight:400;font-size:14px;height:39px;padding:11px 10px}
.browse ul{list-style:none;padding:8px 10px 0}
.browse .grp{font-size:10px;color:#222;display:flex;align-items:center;gap:6px;height:22px}
.browse .sub{font-size:10px;color:#444;padding-left:16px;height:19px}
.tog{width:10px;height:10px;border:1px solid #888;border-radius:2px;background:#ddd;position:relative}
.tog::before{content:"";position:absolute;left:2px;top:3px;width:4px;height:2px;background:#555}
.tog.plus::after{content:"";position:absolute;left:3px;top:2px;width:2px;height:4px;background:#555}
.slider{position:absolute;left:324px;top:143px;width:581px;height:255px;border:1px solid #ccc;background:linear-gradient(135deg,#c98c56 0%,#9b3b25 45%,#7a1b14 70%,#d2a06c 100%)}
.slider-caption{position:absolute;left:4px;bottom:4px;width:236px;height:50px;background:rgba(40,20,15,.55);color:#fff;font-size:23px;font-weight:300;padding:11px 16px;letter-spacing:.3px;white-space:nowrap}
.dots{position:absolute;right:10px;bottom:10px;display:flex;gap:5px}
.dots i{width:12px;height:12px;border-radius:50%;background:#111;display:block}
.dots i.on{background:var(--red);box-shadow:inset 0 0 0 2px #111}
.ad-slot{position:absolute;left:324px;top:413px;width:581px;height:55px;background:linear-gradient(90deg,#1d4a9c,#2457b0 50%,#1d4a9c);border:1px solid #123}

/* content */
.section-title{position:absolute;color:var(--red);font-size:17px;font-weight:400}
.products{position:absolute;left:137px;top:537px;width:543px;height:398px;background:#f4f4f4;border:1px solid var(--line)}
.card{position:absolute;width:160px}
.card .ph{width:154px;height:96px;background:#eaeaea;padding:5px}
.card .ph div{width:100%;height:100%}
.card h3{font-family:"Roboto Condensed",sans-serif;font-weight:400;font-size:15px;margin-top:9px}
.card p{font-size:9.5px;color:#333;line-height:13px;margin-top:1px}
.card .buy{display:flex;justify-content:space-between;align-items:center;margin-top:5px}
.card .price{color:var(--red);font-size:14px;padding-left:2px}
.btn-cart{background:var(--red);color:#fff;font-size:9.5px;padding:3px 5px;border-radius:2px;box-shadow:0 1px 0 var(--red-dark)}
.row-rule{position:absolute;left:12px;top:197px;width:517px;height:1px;background:#ccc}
.aside{position:absolute;left:694px;top:537px;width:212px;height:398px;background:#f4f4f4;border:1px solid var(--line)}
.also{position:absolute;left:12px;width:184px;height:78px;border-bottom:1px dotted #888}
.also .th{position:absolute;left:0;top:9px;width:52px;height:52px}
.also h4{position:absolute;left:63px;top:6px;font-family:"Roboto Condensed",sans-serif;font-weight:400;font-size:15px}
.also p{position:absolute;left:63px;top:27px;font-size:9.5px;line-height:12px;color:#333;width:120px}
.also a{position:absolute;left:63px;top:54px;font-size:9.5px;color:var(--red);text-decoration:none}

/* footer */
.site-footer{position:absolute;left:0;top:946px;width:1040px;height:254px;background:#fff;border-top:3px solid #ddd;box-shadow:inset 0 8px 8px -6px rgba(0,0,0,.12)}
.fcol{position:absolute;top:16px}
.fcol h5{font-size:11px;font-weight:700;margin-bottom:8px}
.fcol ul{list-style:none}
.fcol li{font-size:9px;height:19.2px;color:#222}
.newsletter{position:absolute;right:135px;top:16px;text-align:right}
.newsletter h5{font-size:11px;font-weight:700}
.nl-form{display:flex;gap:4px;margin-top:5px}
.nl-input{width:124px;height:25px;border:1px solid #bbb;font-size:8px;color:#666;padding:7px;text-align:left}
.nl-btn{height:25px;background:linear-gradient(#555,#222);color:#fff;font-size:12px;padding:4px 7px}
.secure{position:absolute;right:135px;top:85px;text-align:right}
.secure h5{font-size:11px;font-weight:700;margin-bottom:6px}
.badges{display:flex;gap:4px;justify-content:flex-end;margin-bottom:6px}
.badges i{display:block;width:28px;height:16px;background:#cfd6e0;border-radius:2px}
.badges.seals i{width:32px;height:26px;background:#d9d2b0;border-radius:50%}
.badges.seals i.sq{border-radius:3px;background:#cfd6e0}
.copy{position:absolute;right:135px;top:181px;font-size:9px}
</style>
</head>
<body>

<header class="site-header">
  <div class="brand"><span class="brand-mark"></span><span class="brand-name">FloorNest.com</span></div>
  <div class="brand-tag">for domestic and heirloom values</div>

  <div class="search">Search
    <svg width="14" height="16" viewBox="0 0 14 16"><circle cx="8.5" cy="5.5" r="4" fill="none" stroke="#fff" stroke-width="2"/><path d="M5.5 8.5 1.5 14" stroke="#fff" stroke-width="2.5" stroke-linecap="round"/></svg>
  </div>

  <div class="top-btns">
    <span class="btn-light">Items (0)</span>
    <span class="btn-light">Total <span class="hi">100</span></span>
    <span class="btn-light">⚲ View Cart</span>
    <span class="btn-light">🔒︎ Checkout</span>
  </div>
  <div class="phone">
    <svg width="12" height="16" viewBox="0 0 12 16"><path d="M3 1h2l1 4-2 1c1 2 2 4 4 5l1-2 3 1v3c-5 1-11-6-9-12z" fill="#999"/></svg>
    Order toll-free: <b>1-888-555-0142</b>
  </div>
  <div class="acct-btns">
    <span class="btn-light">My Account</span>
    <span class="btn-light">Sign In</span>
  </div>
  <div class="live-chat"><span class="chat-ico"></span>LIVE CHAT</div>
</header>

<nav class="main-nav">
  <ul>
    <li style="width:110px">Home</li>
    <li style="width:115px">Selection Guides</li>
    <li style="width:102px">Rug Care</li>
    <li style="width:108px">FAQ</li>
    <li style="width:111px">Return Policy</li>
    <li style="width:113px">Free Shipping</li>
    <li style="width:113px">Clearance Rugs</li>
  </ul>
</nav>

<div class="hero-band"></div>

<aside class="browse">
  <h2>Browse</h2>
  <ul>
    <li class="grp"><span class="tog"></span>RUG THEME</li>
    <li class="sub">Traditional</li>
    <li class="sub">Transitional</li>
    <li class="sub" style="margin-bottom:4px">Casual</li>
    <li class="grp"><span class="tog"></span>COLOR WAY</li>
    <li class="sub">Black</li>
    <li class="sub">Blue</li>
    <li class="sub">Green</li>
    <li class="grp"><span class="tog plus"></span>SIZE</li>
    <li class="grp"><span class="tog plus"></span>SHAPE</li>
    <li class="grp"><span class="tog plus"></span>FIBER CONTENT</li>
    <li class="grp"><span class="tog plus"></span>MFGR. BRAND</li>
    <li class="grp"><span class="tog plus"></span>MFGR.COLLECTION</li>
    <li class="grp"><span class="tog plus"></span>PRICE</li>
  </ul>
</aside>

<section class="slider" role="img" aria-label="Entry hall with a red patterned rug, console table and red armchair">
  <div class="slider-caption">Welcome to Our Site</div>
  <div class="dots"><i></i><i class="on"></i><i></i><i></i></div>
</section>

<div class="ad-slot" role="img" aria-label="Partner advertisement banner"></div>

<h2 class="section-title" style="left:135px;top:508px">Feature Products</h2>
<h2 class="section-title" style="left:694px;top:510px">You may also like</h2>

<section class="products">
  <div class="card" style="left:13px;top:14px">
    <div class="ph"><div role="img" aria-label="Red traditional medallion rug" style="background:linear-gradient(135deg,#7a1c16,#b33a22,#3a1e1a)"></div></div>
    <h3>Heading</h3><p>Lorem Ipsum is simply dummy text of the printing .</p>
    <div class="buy"><span class="price">$50.00</span><span class="btn-cart">Add to Cart</span></div>
  </div>
  <div class="card" style="left:189px;top:14px">
    <div class="ph"><div role="img" aria-label="Cream rug with red floral motif" style="background:linear-gradient(135deg,#e6dccb,#c99a98,#e2d6c3)"></div></div>
    <h3>Heading</h3><p>Lorem Ipsum is simply dummy text of the printing .</p>
    <div class="buy"><span class="price">$50.00</span><span class="btn-cart">Add to Cart</span></div>
  </div>
  <div class="card" style="left:370px;top:14px">
    <div class="ph"><div role="img" aria-label="Brown rug with blue and pink scroll pattern" style="background:linear-gradient(135deg,#4a2420,#8a6070,#5a2c26)"></div></div>
    <h3>Heading</h3><p>Lorem Ipsum is simply dummy text of the printing .</p>
    <div class="buy"><span class="price">$50.00</span><span class="btn-cart">Add to Cart</span></div>
  </div>
  <div class="row-rule"></div>
  <div class="card" style="left:13px;top:213px">
    <div class="ph"><div role="img" aria-label="Rolled brown and gold patterned rug" style="background:linear-gradient(135deg,#3c2414,#8a6a3e,#4a2c1a)"></div></div>
    <h3>Heading</h3><p>Lorem Ipsum is simply dummy text of the printing .</p>
    <div class="buy"><span class="price">$50.00</span><span class="btn-cart">Add to Cart</span></div>
  </div>
  <div class="card" style="left:194px;top:213px">
    <div class="ph"><div role="img" aria-label="Deep red geometric rug" style="background:linear-gradient(135deg,#5a0f10,#9a1c1e,#6a1212)"></div></div>
    <h3>Heading</h3><p>Lorem Ipsum is simply dummy text of the printing .</p>
    <div class="buy"><span class="price">$50.00</span><span class="btn-cart">Add to Cart</span></div>
  </div>
  <div class="card" style="left:370px;top:213px">
    <div class="ph"><div role="img" aria-label="Dark red and beige patterned rug" style="background:linear-gradient(135deg,#3a1a14,#8a5a40,#2a140e)"></div></div>
    <h3>Heading</h3><p>Lorem Ipsum is simply dummy text of the printing .</p>
    <div class="buy"><span class="price">$50.00</span><span class="btn-cart">Add to Cart</span></div>
  </div>
</section>

<aside class="aside">
  <div class="also" style="top:8px"><div class="th" role="img" aria-label="Orange and red rug detail" style="background:linear-gradient(135deg,#c86a2a,#8a2a1a)"></div><h4>Heading</h4><p>Lorem Ipsum is simply dummy text of the...</p><a>Read More &gt;&gt;</a></div>
  <div class="also" style="top:86px"><div class="th" role="img" aria-label="Pale shag rug" style="background:linear-gradient(135deg,#c8c4b4,#8a8a7a)"></div><h4>Heading</h4><p>Lorem Ipsum is simply dummy text of the...</p><a>Read More &gt;&gt;</a></div>
  <div class="also" style="top:164px"><div class="th" role="img" aria-label="Brown and cream shag rug" style="background:linear-gradient(135deg,#3a2a20,#b0a08a)"></div><h4>Heading</h4><p>Lorem Ipsum is simply dummy text of the...</p><a>Read More &gt;&gt;</a></div>
  <div class="also" style="top:246px"><div class="th" role="img" aria-label="Beige rug with red and black border" style="background:linear-gradient(135deg,#d8c8a8,#7a1a14,#1a1a1a)"></div><h4>Heading</h4><p>Lorem Ipsum is simply dummy text of the...</p><a>Read More &gt;&gt;</a></div>
  <div class="also" style="top:324px;border-bottom:none"><div class="th" role="img" aria-label="Cream textured rug" style="background:linear-gradient(135deg,#e0d8c8,#b8ae98)"></div><h4>Heading</h4><p>Lorem Ipsum is simply dummy text of the...</p><a>Read More &gt;&gt;</a></div>
</aside>

<footer class="site-footer">
  <div class="fcol" style="left:135px">
    <h5>Customer Service</h5>
    <ul><li>Shipping</li><li>Return Policy</li><li>Privacy Policy</li><li>Ordering &amp; Delivery Checklist</li><li>Terms of Use</li><li>Terms of Sale</li><li>Contact Us</li><li>Environmental Policy</li></ul>
  </div>
  <div class="fcol" style="left:319px">
    <h5>Resources</h5>
    <ul><li>Product Articles</li><li>Learning Center</li><li>Help</li><li>Refer A Friend</li><li>FloorNest Blog</li><li>Room Scene Viewer</li><li>Site Map</li><li>FAQ</li><li>Customer Testimonials</li><li>Photo Gallery</li></ul>
  </div>
  <div class="fcol" style="left:472px">
    <h5>Corporate Info</h5>
    <ul><li>About FloorNest.com</li><li>Careers</li><li>Affiliates</li></ul>
  </div>
  <div class="newsletter">
    <h5>Newsletter</h5>
    <div class="nl-form"><span class="nl-input">Enter the Email id</span><span class="nl-btn">Subscribe</span></div>
  </div>
  <div class="secure">
    <h5>Secure Payment</h5>
    <div class="badges"><i></i><i></i><i></i><i></i><i></i><i></i></div>
    <div class="badges seals"><i></i><i></i><i class="sq"></i><i class="sq"></i><i class="sq"></i></div>
  </div>
  <div class="copy">Copyrights @ 2013 All Rights Reserved</div>
</footer>

</body>
</html>
```